Business Card Design Project

We are not a new company, but renamed to "Vantorin Kitchens" last year. We specialize in modern high-end cabinetry imports. We would like to communicate a sense of quality and cutting edge technology. Ideally the design would incorporate our logo colors, silver, red and preferably a black, matte background. Though we are open to suggestions.
Logo is attached.
Edit: I have attached rough drafts of the previous cards, this way you will have all necessary content that needs to go on the cards.
Updates
Project Deadline Extended
Reason: We have received a lot of great designs, but due to the sheer number we couldn't respond to all. We will extend the deadline for another 7 days to finalize and provide feedback to designers.
Thank you for your hard work!
Industry/Entity Type
Business
Look and feel
Each slider illustrates characteristics of the customer's brand and the style your logo design should communicate.

```html
<!DOCTYPE html>
<html lang="en">
<head>
<meta charset="utf-8">
<title>Vantorin Kitchens – Business Card</title>
<link rel="stylesheet" href="https://fonts.googleapis.com/css2?family=Arimo:wght@400;700&display=swap">
<style>
  :root {
    --stage: #e8e7ee;
    --card-black: #0b0b0c;
    --silver: #c9c9cc;
    --silver-dark: #9a9a9e;
    --accent-red: #e3171f;
    --text-white: #f4f4f4;
    --text-on-silver: #f7f7f7;
  }
  * { margin: 0; padding: 0; box-sizing: border-box; }
  html, body {
    width: 1200px; height: 987px; overflow: hidden;
    background: var(--stage);
    font-family: "Arimo", Arial, sans-serif;
  }
  .card {
    position: absolute;
    width: 600px; height: 340px;
    border-radius: 28px;
    background: var(--card-black);
    overflow: hidden;
    box-shadow: 0 18px 40px rgba(0,0,0,0.18);
  }
  .card-front { left: 40px; top: 500px; }
  .card-back { left: 560px; top: 110px; }

  .swoosh { position: absolute; inset: 0; }

  .brand {
    position: absolute;
    display: flex; align-items: center; gap: 14px;
    white-space: nowrap;
  }
  .brand-square { width: 24px; height: 24px; background: var(--silver); flex: none; }
  .brand-name {
    font-weight: 700;
    text-transform: uppercase;
    color: var(--silver);
    letter-spacing: 3px;
    font-size: 30px;
    line-height: 1;
  }
  .card-front .brand { left: 112px; top: 48px; }

  .card-back .brand {
    inset: 0;
    justify-content: center;
  }
  .card-back .brand-square { width: 28px; height: 28px; }
  .card-back .brand-name { font-size: 32px; }

  .contact {
    position: absolute;
    left: 150px; top: 106px;
    color: var(--text-white);
    font-size: 17px;
    line-height: 30px;
  }
  .contact-line { display: flex; align-items: center; gap: 8px; white-space: nowrap; }
  .contact-line svg { width: 15px; height: 15px; flex: none; }
  .contact-line .gap { width: 14px; }

  .holder {
    position: absolute;
    left: 40px; bottom: 20px;
    font-size: 18px;
    font-weight: 700;
    color: var(--text-on-silver);
    text-transform: uppercase;
    letter-spacing: 0.5px;
    white-space: nowrap;
  }
  .holder .role { color: var(--accent-red); text-transform: none; }
</style>
</head>
<body>

<section class="card card-back" aria-label="Business card back">
  <div class="brand">
    <span class="brand-square"></span>
    <span class="brand-name">Vantorin Kitchens</span>
  </div>
</section>

<section class="card card-front" aria-label="Business card front">
  <svg class="swoosh" viewBox="0 0 600 340" aria-hidden="true">
    <defs>
      <linearGradient id="silver-band" x1="0" y1="0" x2="0" y2="1">
        <stop offset="0" stop-color="#c4c4c8"/>
        <stop offset="1" stop-color="#a2a2a6"/>
      </linearGradient>
    </defs>
    <path d="M0 122 C 40 232, 240 302, 600 334 L600 340 L0 340 Z" fill="url(#silver-band)"/>
    <path d="M0 116 C 40 226, 240 296, 600 328" fill="none" stroke="#2e2e30" stroke-width="4"/>
    <path d="M0 108 C 40 218, 240 288, 600 320" fill="none" stroke="var(--accent-red)" stroke-width="5"/>
  </svg>

  <div class="brand">
    <span class="brand-square"></span>
    <span class="brand-name">Vantorin Kitchens</span>
  </div>

  <div class="contact">
    <div class="contact-line">
      <svg viewBox="0 0 16 16" aria-hidden="true"><circle cx="8" cy="8" r="7.5" fill="var(--accent-red)"/><path d="M5 4.5 l2 0 l0.6 2 l-1 0.8 a5 5 0 0 0 2.1 2.1 l0.8 -1 l2 0.6 l0 2 a7 7 0 0 1 -6.5 -6.5z" fill="#fff"/></svg>
      <span>555.201.0144</span><span class="gap"></span>
      <svg viewBox="0 0 16 16" aria-hidden="true"><rect x="2" y="6" width="12" height="7" rx="1.5" fill="var(--accent-red)"/><rect x="4" y="2" width="8" height="5" fill="var(--accent-red)"/><rect x="5" y="9" width="6" height="1.5" fill="#000"/></svg>
      <span>555.201.0188</span>
    </div>
    <div class="contact-line">
      <svg viewBox="0 0 16 16" aria-hidden="true"><rect x="4" y="1" width="8" height="14" rx="1.5" fill="var(--accent-red)"/><rect x="5.5" y="3" width="5" height="7" fill="#000"/></svg>
      <span>555.318.4620</span><span class="gap"></span>
      <svg viewBox="0 0 16 16" aria-hidden="true"><rect x="1" y="3.5" width="14" height="9" rx="1" fill="var(--accent-red)"/><path d="M1.5 4 L8 9 L14.5 4" fill="none" stroke="#000" stroke-width="1.2"/></svg>
      <span>marcus@vantorinkitchens.ca</span>
    </div>
    <div class="contact-line">
      <span>1180 - 42 Ave. Halvern, AB T0X 4Q2</span>
    </div>
  </div>

  <p class="holder">Marcus Holt, <span class="role">Director</span></p>
</section>

</body>
</html>
```